Design a website for our small self storage business

We're looking for a freelance web designer who can produce a good-looking design for our small business website (no coding necessary). We will provide a list of pages to design, along with content outlines.

Key skills:
- Graphic design
- Responsive web design
- Proficiency with a modern web design tool such as Figma, Adobe Xd, or InVision

Please send relevant previous work (preferably in an inspectable format such as Figma or Invision).

```html
<!DOCTYPE html>
<html lang="en">
<head>
<meta charset="utf-8">
<title>Harbor Self Storage — Van Nuys</title>
<link rel="stylesheet" href="https://fonts.googleapis.com/css2?family=Montserrat:wght@700;800;900&family=Mulish:wght@400;600;700;800&display=swap">
<style>
:root{
  --navy:#0d4a8a;
  --navy-deep:#063a72;
  --red:#e31b23;
  --ink:#222;
  --text:#444;
  --grey-bg:#e6e7e9;
  --white:#fff;
}
*{box-sizing:border-box;margin:0;padding:0}
html,body{width:1200px;height:3031px;overflow:hidden;background:var(--white)}
body{position:relative;font-family:"Mulish",sans-serif;color:var(--ink)}
.abs{position:absolute}
.btn{position:absolute;background:var(--red);color:var(--white);font-family:"Montserrat",sans-serif;font-weight:800;text-transform:uppercase;display:flex;align-items:center;justify-content:center;text-decoration:none}

/* header */
.brand{position:absolute;display:flex;align-items:center;gap:10px;color:var(--navy);font-family:"Mulish",sans-serif;font-weight:800;text-transform:uppercase;line-height:1.05}
.brand .mark{background:var(--red);flex:none}
.header-info{position:absolute;top:22px;font-size:16px;font-weight:600;line-height:20px}
.header-info .accent{color:var(--navy);font-weight:800}
.header-divider{position:absolute;width:2px;height:40px;background:var(--navy);top:22px}
.nav{position:absolute;top:81px;left:648px;display:flex;font-size:16px;font-weight:600;text-transform:uppercase}
.nav a{color:var(--ink);text-decoration:none;height:25px;line-height:25px;padding:0 8px}
.nav a.active{background:var(--red);color:var(--white)}

/* hero */
.hero-photo{position:absolute;top:129px;left:0;width:1200px;height:580px;background:linear-gradient(90deg,#1d2f8f 0%,#3442a0 10%,#d9dbe0 30%,#c9c3b8 42%,#2c3a9c 58%,#1f2f90 100%)}
.hero-title{position:absolute;left:902px;top:285px;color:var(--white);font-family:"Montserrat",sans-serif;font-weight:800;font-size:34px;line-height:46px;letter-spacing:-.5px;white-space:nowrap;text-transform:uppercase}
.hero-dots{position:absolute;top:609px;left:566px;display:flex;gap:6px}
.hero-dots span{width:8px;height:8px;background:var(--white)}
.hero-dots span.on{background:var(--red)}

/* service cards */
.card{position:absolute;top:700px;width:461px;height:532px;background:var(--white);box-shadow:0 2px 8px rgba(0,0,0,.12);text-align:center}
.card-photo{width:100%;height:317px}
.card h3{margin-top:29px;font-family:"Mulish",sans-serif;font-weight:800;font-size:16px;letter-spacing:.3px}
.card p{margin:18px auto 0;width:380px;font-size:13.5px;line-height:19.5px;color:var(--text)}
.card .btn{left:180px;top:475px;width:102px;height:29px;font-size:12px}

/* welcome */
.welcome-bg{position:absolute;top:1282px;left:0;width:1200px;height:553px;background:linear-gradient(180deg,#eef0f4,#f4f5f7)}
.welcome-heading{position:absolute;right:742px;top:1350px;text-align:right;font-family:"Mulish",sans-serif;font-weight:800;font-size:21px;line-height:32px;text-transform:uppercase;color:var(--navy)}
.welcome-heading .lead{color:var(--red)}
.welcome-rule{position:absolute;left:503px;top:1323px;width:1px;height:148px;background:#8c9bb5}
.welcome-text{position:absolute;left:553px;top:1320px;width:510px;font-size:13.5px;line-height:18.5px;color:var(--ink)}
.welcome-text p+p{margin-top:18px}

/* features */
.feature{position:absolute;top:1870px;width:260px;text-align:center}
.feature .stem{margin:0 auto;width:2px;height:163px;position:relative}
.feature .stem svg{position:absolute;left:-36px;top:45px}
.feature h3{margin-top:24px;font-family:"Mulish",sans-serif;font-weight:800;font-size:16.5px;color:var(--navy);text-transform:uppercase}
.feature p{margin:16px auto 0;width:253px;font-size:13.5px;line-height:19px;color:var(--text)}

/* bring section */
.bring{position:absolute;top:2223px;left:0;width:1200px;height:460px;background:linear-gradient(90deg,#0a3d7c,#0d4a8a 45%,#0b4384);text-align:center;color:var(--white)}
.bring h2{margin-top:95px;font-family:"Montserrat",sans-serif;font-weight:800;font-size:31px}
.bring p{margin:28px auto 0;width:730px;font-size:16px;line-height:22.5px}

/* footer */
.footer-bg{position:absolute;top:2660px;left:0;width:1200px;height:371px;background:var(--grey-bg)}
.footer-brand{position:absolute;left:0;top:2675px;width:1200px;flex-direction:column;gap:12px;font-size:26px;text-align:center;justify-content:center}
.footer-nav{position:absolute;top:2794px;left:0;width:1200px;text-align:center;font-size:16px;font-weight:600;word-spacing:2px}
.footer-contact{position:absolute;top:2837px;left:0;width:1200px;text-align:center;font-size:15.5px}
.footer-hours{position:absolute;top:2882px;left:0;width:1200px;text-align:center;font-size:15.5px;font-weight:600}
.footer-hours .accent{color:var(--navy);font-weight:800}
.footer-line{position:absolute;top:2893px;height:2px;background:var(--navy);width:180px}
.pay{position:absolute;top:2935px;left:479px;display:flex;gap:10px}
.pay span{width:53px;height:32px;border-radius:3px}
.copy{position:absolute;top:2993px;left:0;width:1200px;text-align:center;font-size:14.5px}
</style>
</head>
<body>

<header>
  <div class="brand" style="left:132px;top:36px;font-size:19px">
    <span class="mark" style="width:34px;height:34px"></span>
    <span>Harbor Self Storage<br>Van Nuys</span>
  </div>
  <svg class="abs" style="left:641px;top:28px" width="30" height="30" viewBox="0 0 30 30" aria-hidden="true">
    <circle cx="15" cy="15" r="13" fill="none" stroke="#0d4a8a" stroke-width="1.6"/>
    <path d="M15 7v8l5 3" fill="none" stroke="#0d4a8a" stroke-width="1.6"/>
  </svg>
  <div class="header-divider" style="left:681px"></div>
  <div class="header-info" style="left:698px">7 DAYS A WEEK<br><span class="accent">9:30 AM - 5:30 PM</span></div>
  <svg class="abs" style="left:864px;top:28px" width="28" height="28" viewBox="0 0 28 28" aria-hidden="true">
    <path d="M6 3l5 5-3 3c2 4 5 7 9 9l3-3 5 5-4 4C12 25 3 16 2 7z" fill="none" stroke="#0d4a8a" stroke-width="1.6"/>
  </svg>
  <div class="header-divider" style="left:901px"></div>
  <div class="header-info" style="left:917px;top:20px"><span class="accent" style="font-size:14px">CALL US</span><br><span class="accent" style="font-size:20px;line-height:26px">(818) 555 - 0142</span></div>
  <nav class="nav">
    <a class="active" href="#">Home</a>
    <a href="#" style="margin-left:23px">Units</a>
    <a href="#" style="margin-left:36px">Pay Online</a>
    <a href="#" style="margin-left:24px">Contact Us</a>
  </nav>
</header>

<section>
  <div class="hero-photo" role="img" aria-label="Indoor storage corridor lined with blue roll-up unit doors"></div>
  <h1 class="hero-title">Harbor<br>Self Storage<br>In Van Nuys</h1>
  <a class="btn" href="#" style="left:906px;top:436px;width:128px;height:40px;font-size:15px">Read More</a>
  <div class="hero-dots"><span></span><span></span><span class="on"></span><span></span><span></span></div>
  <svg class="abs" style="left:0;top:630px" width="1200" height="90" viewBox="0 0 1200 90" aria-hidden="true">
    <path d="M0 60 Q600 -10 1200 60 L1200 90 L0 90Z" fill="#fff"/>
    <path d="M0 72 Q600 -5 1200 72 L1200 82 Q600 5 0 82Z" fill="#0d4a8a"/>
  </svg>
</section>

<section>
  <article class="card" style="left:131px">
    <div class="card-photo" role="img" aria-label="Corridor of red metal drive-up storage units" style="background:linear-gradient(90deg,#9e1a1f,#c92a2c 30%,#6b6e72 50%,#c92a2c 70%,#9e1a1f)"></div>
    <h3>DRIVE-UP SPACES</h3>
    <p>There are many variations of passages of Lorem Ipsum available, but the majority have suffered alteration in some form, by injected humour, or randomised words which don't look even slightly believable</p>
    <a class="btn" href="#">Read More</a>
  </article>
  <article class="card" style="left:606px">
    <div class="card-photo" role="img" aria-label="Two customers with cardboard boxes beside green storage units" style="background:linear-gradient(90deg,#d8dbd6,#c9c2b4 40%,#b89a72 60%,#8fc43a 80%,#7cb82f)"></div>
    <h3>JUST SHOW UP WITH YOUR STUFF</h3>
    <p>There are many variations of passages of Lorem Ipsum available, but the majority have suffered alteration in some form, by injected humour, or randomised words which don't look even slightly believable</p>
    <a class="btn" href="#">Read More</a>
  </article>
</section>

<section>
  <div class="welcome-bg"></div>
  <h2 class="welcome-heading"><span class="lead">Welcome to</span><br>Harbor Self Storage<br>in Van Nuys</h2>
  <div class="welcome-rule"></div>
  <div class="welcome-text">
    <p>Harbor Self Storage Van Nuys Located on Maple St. between Birch Ave. and Cedar Ave. near Van Nuys City Hall in San Fernando Valley.</p>
    <p>For most people, finding self storage is a matter of locating the intersection of convenience, security, quality, and price. This isn't such a simple equation. On our website you can find our self storage price quickly and easily. We've got a great selection of storage units of various sizes in the heart of San Fernando Valley - downtown area Van Nuys.</p>
  </div>
  <a class="btn" href="#" style="left:557px;top:1485px;width:102px;height:30px;font-size:12px">Read More</a>
  <svg class="abs" style="left:0;top:1476px" width="1200" height="360" viewBox="0 0 1200 360" role="img" aria-label="Outdoor row of yellow roll-up storage units under grey metal siding">
    <defs>
      <linearGradient id="lotTone" x1="0" x2="1">
        <stop offset="0" stop-color="#7b8088"/>
        <stop offset=".35" stop-color="#c9a928"/>
        <stop offset=".55" stop-color="#e0c23a"/>
        <stop offset=".7" stop-color="#a8acb2"/>
        <stop offset="1" stop-color="#b9bec6"/>
      </linearGradient>
    </defs>
    <polygon points="131,0 700,100 1200,150 1200,346 131,346" fill="url(#lotTone)"/>
    <rect x="0" y="346" width="1200" height="14" fill="#0d4a8a"/>
  </svg>
</section>

<section>
  <div class="feature" style="left:143px">
    <div class="stem" style="background:var(--navy)">
      <svg width="74" height="74" viewBox="0 0 74 74" aria-hidden="true"><circle cx="37" cy="37" r="37" fill="#0d4a8a"/><circle cx="40" cy="30" r="11" fill="none" stroke="#fff" stroke-width="2.5"/><text x="40" y="35" text-anchor="middle" font-family="Mulish,sans-serif" font-weight="800" font-size="14" fill="#fff">$</text><path d="M16 46h12l8 4h12v4H22" fill="none" stroke="#fff" stroke-width="2.5"/></svg>
    </div>
    <h3>Affordable</h3>
    <p>There are many variations of passages of Lorem Ipsum available, but the majority have suffered alteration in some form, by injected humour, or randomised words.</p>
  </div>
  <div class="feature" style="left:471px">
    <div class="stem" style="background:var(--red)">
      <svg width="74" height="74" viewBox="0 0 74 74" aria-hidden="true"><circle cx="37" cy="37" r="37" fill="#e31b23"/><path d="M29 32v-6a8 8 0 0 1 16 0v6" fill="none" stroke="#fff" stroke-width="3"/><rect x="24" y="32" width="26" height="22" rx="3" fill="#fff"/><path d="M31 43l4 4 8-8" fill="none" stroke="#e31b23" stroke-width="3"/></svg>
    </div>
    <h3>Secure</h3>
    <p>There are many variations of passages of Lorem Ipsum available, but the majority have suffered alteration in some form, by injected humour, or randomised words.</p>
  </div>
  <div class="feature" style="left:814px">
    <div class="stem" style="background:var(--navy)">
      <svg width="74" height="74" viewBox="0 0 74 74" aria-hidden="true"><circle cx="37" cy="37" r="37" fill="#0d4a8a"/><path d="M20 54V30l17-10 17 10v24z" fill="#fff"/><rect x="29" y="38" width="16" height="16" fill="#0d4a8a"/><path d="M29 43h16M29 48h16M34 38v16M40 38v16" stroke="#fff" stroke-width="1.5"/></svg>
    </div>
    <h3>Convenient</h3>
    <p>There are many variations of passages of Lorem Ipsum available, but the majority have suffered alteration in some form, by injected humour, or randomised words.</p>
  </div>
</section>

<section class="bring" role="region" aria-label="What to bring">
  <h2>What should I bring to rent a space?</h2>
  <p>But I must explain to you how all this mistaken idea of denouncing pleasure and praising pain was born and I will give you a complete account of the system, and expound the actual teachings of the great explorer of the truth, the master-builder of human happiness. No one rejects, dislikes, or avoids pleasure itself, because it is pleasure, but because those who do not know how to pursue pleasure rationally encounter consequences that are extremely painful</p>
</section>

<footer>
  <div class="footer-bg"></div>
  <svg class="abs" style="left:0;top:2590px" width="1200" height="90" viewBox="0 0 1200 90" aria-hidden="true">
    <path d="M0 80 Q600 -5 1200 80 L1200 90 L0 90Z" fill="#e6e7e9"/>
    <path d="M0 68 Q600 -20 1200 68 L1200 80 Q600 -5 0 80Z" fill="#0d4a8a"/>
  </svg>
  <div class="brand footer-brand">
    <span class="mark" style="width:40px;height:40px"></span>
    <span>Harbor Self Storage<br>Van Nuys</span>
  </div>
  <div class="footer-nav">HOME &nbsp;&nbsp;| &nbsp;&nbsp;UNITS &nbsp;&nbsp;| &nbsp;&nbsp;PAY ONLINE &nbsp;&nbsp;| &nbsp;&nbsp;CONTACT US</div>
  <div class="footer-contact">2480 Maple Street, Van Nuys, CA 91401 &nbsp;&nbsp;| &nbsp;&nbsp;(818) 555-0142 &nbsp;&nbsp;| &nbsp;&nbsp;info@harborstoragela.com</div>
  <div class="footer-line" style="left:267px"></div>
  <div class="footer-hours">7 DAYS A WEEK <span class="accent">9:30 AM - 5:30 PM</span></div>
  <div class="footer-line" style="left:748px"></div>
  <div class="pay" aria-label="Accepted payment cards">
    <span style="background:#1a3d8f"></span>
    <span style="background:#d8342a"></span>
    <span style="background:#2a6fc0"></span>
    <span style="background:#5a9bd5"></span>
  </div>
  <div class="copy">© 2022 Harbor Self Storage</div>
</footer>

</body>
</html>
```